Payment company requires web design

We need a web design for a new company based in Singapore.

The company focuses on providing 2 key products: 1) an alternative payment option (i.e. like quib or trelloquin options) on the traditional checkout process 2) a replacement/outsource of a merchants payment page. Key in the UX flow is a end customer dashboard that manages all payments.

We look to provide a simple, fluid and easy to use payment process. The dashboard is minimalistic that allows easy navigation, review of transactions and all available options through gamification.

The final design should communicate ease of use, flexibility and transparency.

Target Market(s)

The value is for the merchant - retail/travel/insurance companies. However its the merchant's end customers that are the target and who the UX is built for.

Industry/Entity Type

It Company

Logo Text

zelnar

Number of Pages Required

5+ page

Colors
ec1f27

Requirements
Must have
• 7 pages mimicking UX flow
• payment page * 2 - 1) alternative payment type 2) outsource of merchants payment page to our business
• our landing page
• end customer verification page
• end customer registration
• customer dashboard
• UX flow in attached file
Nice to have
• open to ideas
• have asked for the logo to be added
• logo to have the colour red (chinese for prosperity)
• the company is all about flexibility, transparency in personal finance management with the option of instalment payments

```html
<!DOCTYPE html>
<html lang="en">
<head>
<meta charset="utf-8">
<title>Zelnar – Flexible Payments</title>
<link href="https://fonts.googleapis.com/css2?family=Open+Sans:wght@400;600;700&display=swap" rel="stylesheet">
<style>
:root{
  --red:#ec1f27;
  --ink:#2b2b2b;
  --body:#555;
  --muted:#777;
  --band:#f0f0f0;
  --line:#e2e2e2;
  --white:#fff;
}
*{box-sizing:border-box;margin:0;padding:0}
html,body{width:1200px;height:2293px;overflow:hidden}
body{position:relative;font-family:"Open Sans",Arial,sans-serif;color:var(--ink);background:var(--white)}
a{text-decoration:none}
.abs{position:absolute}
.btn{position:absolute;background:var(--red);color:var(--white);font-weight:700;text-transform:uppercase;display:flex;align-items:center;justify-content:center;letter-spacing:.2px;text-decoration:none}

/* header */
.site-header{position:absolute;left:0;top:0;width:1200px;height:89px;border-top:3px solid var(--red);background:var(--white);box-shadow:0 2px 4px rgba(0,0,0,.08);z-index:2}
.brand{position:absolute;left:162px;top:27px;font-size:34px;font-weight:700;color:var(--red);letter-spacing:1px;text-transform:uppercase;line-height:1}
.nav a{position:absolute;top:40px;font-size:12px;color:var(--ink);text-transform:uppercase;font-weight:600}
.nav a.active{color:var(--red)}
.nav-marker{position:absolute;left:516px;top:86px;width:0;height:0;border-left:8px solid transparent;border-right:8px solid transparent;border-top:7px solid var(--red)}
.signup{left:969px;top:34px;width:69px;height:30px;font-size:11px}

/* hero */
.hero{position:absolute;left:0;top:89px;width:1200px;height:504px;background:#efefef}
.hero-photo{position:absolute;left:489px;top:0;width:711px;height:504px;background:linear-gradient(135deg,#f4f4f4 0%,#e8e4df 45%,#d9d3cc 70%,#f2f2f2 100%)}
.hero-kicker{position:absolute;left:162px;top:152px;font-size:23px;color:#333}
.hero-title{position:absolute;left:162px;top:188px;font-size:31px;color:var(--red);font-weight:600}
.hero-text{position:absolute;left:162px;top:244px;width:500px;font-size:14.5px;line-height:24px;color:var(--body)}
.register{left:162px;top:322px;width:125px;height:37px;font-size:15px;font-weight:600}
.slide-arrow{position:absolute;top:237px;width:32px;height:32px;border:1px solid #bbb;border-radius:50%;display:flex;align-items:center;justify-content:center}

/* welcome */
.welcome-title{position:absolute;left:162px;top:640px;font-size:21px;color:var(--red);font-weight:600}
.welcome-lead{position:absolute;left:162px;top:681px;width:430px;font-size:14px;line-height:23px;color:#333}
.welcome-body{position:absolute;left:162px;top:744px;width:425px;font-size:10.5px;line-height:20px;color:var(--muted)}
.readmore{font-size:10.5px;height:33px;width:96px}
.welcome-art{position:absolute;left:619px;top:634px;width:400px;height:300px;background:radial-gradient(ellipse at 50% 55%,#d3e9ee 0%,#eef5f6 50%,#fff 100%)}

/* steps */
.steps{position:absolute;left:0;top:949px;width:1200px;height:399px;background:var(--band)}
.section-title{position:absolute;left:0;width:1200px;text-align:center;font-size:23px;font-weight:600;color:#333;text-transform:uppercase}
.step{position:absolute;top:123px;width:240px;text-align:center}
.step-icon{margin:0 auto;width:96px;height:96px;border:3px solid var(--red);border-radius:50%;display:flex;align-items:center;justify-content:center;background:var(--band)}
.step-name{margin-top:29px;font-size:14px;font-weight:600;text-transform:uppercase;color:#333}
.step-text{margin-top:14px;font-size:11px;line-height:19px;color:var(--body);padding:0 28px}

/* reasons */
.card{position:absolute;top:1446px;width:276px}
.card-img{width:276px;height:150px;border:2px solid #e6e6e6}
.card-title{margin-top:15px;font-size:15.5px;font-weight:700;color:#222}
.card-text{margin-top:9px;font-size:10.8px;line-height:19px;color:var(--body)}
.card .btn{position:relative;margin-top:19px}

/* cta */
.cta{position:absolute;left:0;top:1811px;width:1200px;height:207px;background:var(--band)}
.cta-title{position:absolute;left:0;top:54px;width:1200px;text-align:center;font-size:25px;line-height:33px;color:#333;font-weight:600}
.cta .btn{left:534px;top:140px;width:133px;height:33px;font-size:10.5px}

/* footer */
.footer-col{position:absolute;top:2077px}
.footer-col h4{font-size:12px;font-weight:700;text-transform:uppercase;color:#222;margin-bottom:22px}
.footer-col li{list-style:none;font-size:11px;line-height:21px;color:#444}
.social{display:flex;gap:4px}
.social span{width:28px;height:28px;border-radius:50%;display:block}
.copy{font-size:11px;color:#333;margin-top:14px;line-height:18px}
.footer-rule{position:absolute;left:0;top:2289px;width:1200px;height:1px;background:var(--line)}
</style>
</head>
<body>

<header class="site-header">
  <div class="brand">Zelnar</div>
  <nav class="nav">
    <a class="active" href="#" style="left:506px">Home</a>
    <a href="#" style="left:576px">About</a>
    <a href="#" style="left:651px">Merchant Payment</a>
    <a href="#" style="left:806px">Outsourced Payment</a>
  </nav>
  <a class="btn signup" href="#">Sign Up</a>
  <div class="nav-marker"></div>
</header>

<section class="hero">
  <div class="hero-photo" role="img" aria-label="Photo of a happy young couple at a laptop paying online with a card"></div>
  <p class="hero-kicker">We are about flexibility transparency</p>
  <h1 class="hero-title">in personal finance management</h1>
  <p class="hero-text">Lorem ipsum dolor sit amet, consectetur adipiscing elit, sed do eiusmod<br>tempor incididunt ut laborelorem ipmo.</p>
  <a class="btn register" href="#">Register</a>
  <div class="slide-arrow" style="left:29px"><svg width="10" height="12" viewBox="0 0 10 12"><path d="M7 1 2 6l5 5" fill="none" stroke="#aaa" stroke-width="1.5"/></svg></div>
  <div class="slide-arrow" style="left:1140px"><svg width="10" height="12" viewBox="0 0 10 12"><path d="M3 1l5 5-5 5" fill="none" stroke="#aaa" stroke-width="1.5"/></svg></div>
</section>

<section class="welcome">
  <h2 class="welcome-title">WELCOME TO ZELNAR</h2>
  <p class="welcome-lead">Lorem ipsum dolor sit amet, consectetur adipiscing elit, sed deiu<br>sm tempor incididunt ut laborelorem ipmo.</p>
  <p class="welcome-body">Sed ut perspiciatis unde omnis iste natus error sit voluptatem accusantium dolore mq ue laudantium, totam rem aperiam, eaque ipsa quae ab illo inventore veritatis et quasi archit ecto beatae vitae dicta sunt explicabo. Nemo enim ipsam volupta tem quia volup tas sit aspernatur aut odit aut fugit, sed quia conse quun tur mag ni dolores eos qui rati one voluptatem sequi nesciunt.</p>
  <a class="btn readmore" href="#" style="left:162px;top:864px">Read More »</a>
  <div class="welcome-art" role="img" aria-label="Illustration of a small store on a tablet with an online payments speech bubble and coins"></div>
</section>

<section class="steps">
  <h2 class="section-title" style="top:46px">How does it work?</h2>
  <svg class="abs" style="left:320px;top:131px" width="580" height="50" viewBox="0 0 580 50" aria-hidden="true">
    <path d="M0 30 Q40 5 85 28" fill="none" stroke="#dcdcdc" stroke-width="6"/>
    <path d="M235 38 Q275 10 320 30" fill="none" stroke="#dcdcdc" stroke-width="6"/>
    <path d="M470 30 Q510 5 555 28" fill="none" stroke="#dcdcdc" stroke-width="6"/>
  </svg>
  <div class="step" style="left:129px">
    <div class="step-icon"><svg width="44" height="40" viewBox="0 0 44 40"><ellipse cx="22" cy="26" rx="17" ry="11" fill="#ec1f27"/><circle cx="22" cy="8" r="7" fill="#ec1f27"/><rect x="11" y="33" width="5" height="6" fill="#ec1f27"/><rect x="28" y="33" width="5" height="6" fill="#ec1f27"/><text x="22" y="11" font-size="9" fill="#fff" text-anchor="middle" font-family="Arial,sans-serif">$</text></svg></div>
    <div class="step-name">Merchant</div>
    <p class="step-text">Sed ut perspiciatis unde otsrs itvoluptatem accusan tium dolore mq ue laudpta te iu dololorlo</p>
  </div>
  <div class="step" style="left:365px">
    <div class="step-icon"><svg width="40" height="40" viewBox="0 0 40 40"><rect x="14" y="4" width="20" height="32" fill="#ec1f27"/><rect x="18" y="8" width="12" height="24" fill="#fff"/><path d="M2 20h16M12 14l6 6-6 6" stroke="#ec1f27" stroke-width="3" fill="none"/></svg></div>
    <div class="step-name">Sign In</div>
    <p class="step-text">Sed ut perspiciatis unde otsrs itvoluptatem accusan tium dolore mq ue laudpta te iu dololorlo</p>
  </div>
  <div class="step" style="left:600px">
    <div class="step-icon"><svg width="44" height="36" viewBox="0 0 44 36"><rect x="4" y="2" width="34" height="22" rx="2" fill="#ec1f27" transform="rotate(-8 21 13)"/><rect x="8" y="10" width="34" height="22" rx="2" fill="#ec1f27" stroke="#fff" stroke-width="1.5"/><rect x="8" y="15" width="34" height="4" fill="#fff"/><circle cx="35" cy="26" r="2.5" fill="#fff"/></svg></div>
    <div class="step-name">Card Network</div>
    <p class="step-text">Sed ut perspiciatis unde otsrs itvoluptatem accusan tium dolore mq ue laudpta te iu dololorlo</p>
  </div>
  <div class="step" style="left:834px">
    <div class="step-icon"><svg width="32" height="40" viewBox="0 0 32 40"><path d="M8 18V11a8 8 0 0 1 16 0v7" stroke="#ec1f27" stroke-width="4" fill="none"/><rect x="3" y="18" width="26" height="20" rx="2" fill="#ec1f27"/></svg></div>
    <div class="step-name">Easy Checkout</div>
    <p class="step-text">Sed ut perspiciatis unde otsrs itvoluptatem accusan tium dolore mq ue laudpta te iu dololorlo</p>
  </div>
</section>

<section class="reasons">
  <h2 class="section-title" style="top:1384px">More reasons to use Zelnar</h2>
  <article class="card" style="left:162px">
    <div class="card-img" role="img" aria-label="Photo of a phone being tapped on a card terminal" style="background:linear-gradient(135deg,#5a3a48,#a88a8e 55%,#d9cfcf)"></div>
    <h3 class="card-title">Lorem ipsum dolor sit ame</h3>
    <p class="card-text">Sed ut p loerspiciatis unde omnis iste natus error sit volup tatem accusantium dolore mq uloe laud antium, tota m rem aperiam, eaque ipsa quae ab.</p>
    <a class="btn readmore" href="#">Read More »</a>
  </article>
  <article class="card" style="left:464px">
    <div class="card-img" role="img" aria-label="Photo of hands using a tablet while holding a payment card" style="background:linear-gradient(135deg,#7e97ad,#c9c3bc 55%,#eee)"></div>
    <h3 class="card-title">Lorem ipsum dolor sit ame</h3>
    <p class="card-text">Sed ut p loerspiciatis unde omnis iste natus error sit volup tatem accusantium dolore mq uloe laud antium, tota m rem aperiam, eaque ipsa quae ab.</p>
    <a class="btn readmore" href="#">Read More »</a>
  </article>
  <article class="card" style="left:766px">
    <div class="card-img" role="img" aria-label="Photo of a customer entering a PIN on a card terminal at a counter" style="background:linear-gradient(135deg,#2f2a2a,#8a6e60 50%,#7fa0c6)"></div>
    <h3 class="card-title">Lorem ipsum dolor sit ame</h3>
    <p class="card-text">Sed ut p loerspiciatis unde omnis iste natus error sit volup tatem accusantium dolore mq uloe laud antium, tota m rem aperiam, eaque ipsa quae ab.</p>
    <a class="btn readmore" href="#">Read More »</a>
  </article>
</section>

<section class="cta">
  <h2 class="cta-title">Ready to get started? Get in touch,<br>or create an account</h2>
  <a class="btn" href="#">Create Account »</a>
</section>

<footer>
  <div class="footer-col" style="left:162px"><h4>Products</h4><ul><li>Payments</li><li>Instalments</li><li>Linkway</li><li>Passline</li><li>Ledgerbook</li></ul></div>
  <div class="footer-col" style="left:345px"><h4>Developers</h4><ul><li>Documentation</li><li>API reference</li><li>API status</li><li>Open source</li><li>Pricing</li><li>Customers</li></ul></div>
  <div class="footer-col" style="left:535px"><h4>What we do</h4><ul><li>Sed ut perspiciatis</li><li>Qnde omnis iste n</li><li>Wtus error sit voluptat</li><li>em accusantiu</li><li>Gdoloremque</li></ul></div>
  <div class="footer-col" style="left:717px"><h4>Company</h4><ul><li>Company info</li><li>News</li><li>Investors</li><li>Sed ut perspici</li><li>em accusantiu</li></ul></div>
  <div class="footer-col" style="left:865px"><h4>Follow us</h4>
    <div class="social">
      <span role="img" aria-label="Social network link" style="background:#5aaee0"></span>
      <span role="img" aria-label="Social network link" style="background:#3b5b9a"></span>
      <span role="img" aria-label="Social network link" style="background:#1b78a8"></span>
      <span role="img" aria-label="Social network link" style="background:#d9503f"></span>
    </div>
    <p class="copy">© 2016 All Copyrights are Reserved.<br>Privacy Policy &nbsp; Sitemap</p>
  </div>
  <div class="footer-rule"></div>
</footer>

</body>
</html>
```